Upstart Retirement Planning Firm needs help with business card design

Harborview Nest Advisors, LLC is looking for help with business card design. We give advice on investments, insurance, and other financial matters related to retirement. There are some required disclosures that we will provide but mostly we are looking for a professional, classy business card that reflects the theme we have chosen. We have a logo that is attached but we would like to add a phrase; "Turning Your Earned Income Into Retirement Income"

Doubled sided only so that we can add the required disclosures (needed for our industry) on the back of the card. We will provide the exact words for this in 1-2 days.

Target Market(s)

Retirees and Pre-retirees. Professionals 50+ years old

Industry/Entity Type

Financial Planning

Contact Information for Business Card

We currently have two people who will need separate cards so we'd like to have a template so that we can add names for new cards in the future.

For the first run, please show the following information.

Gregor Pelham, MBA, ChFC®, CLU®
Financial Advisor, Registered Representative
gpelham@harborviewnest.example
Phone: (555) 318-2946
Toll Free Fax: (800) 555-0193

Address is
2187 Meadowlark Ridge Rd.
Suite K418
Virginia Beach, VA 23999

Colors
3277b5

Requirements
Must have
• Logo, contact info, small phase to describe business (in description), required legal disclosures on back of the card as follows (in small font)
• Gregor Pelham is a registered representative of and offers securities through Brightmoor Capital Brokerage Corporation, Member FNQX. Brightmoor Capital Brokerage Corporation is a member of the Brightmoor Capital Alliance which is the marketing name for Brightmoor Holding Corporation and its affiliates.
Nice to have
• Rounded edges, raised letters
Should not have
• any colors that aren't in the logo (other than black for font)

```html
<!DOCTYPE html>
<html lang="en">
<head>
<meta charset="utf-8">
<title>Harborview Nest Advisors — Business Card</title>
<link rel="stylesheet" href="https://fonts.googleapis.com/css2?family=Libre+Baskerville:wght@400&display=swap">
<style>
  :root {
    --brand-blue: #3277b5;
    --deep-blue: #1f5a9e;
    --steel-gray: #9a9da3;
    --ink: #1d1d1f;
    --card: #ffffff;
    --backdrop: #dcdcdc;
    --divider: #e6e7ea;
  }
  * { box-sizing: border-box; margin: 0; padding: 0; }
  html, body {
    width: 1200px; height: 1200px; overflow: hidden;
    background: var(--backdrop);
    font-family: "Libre Baskerville", Georgia, serif;
    color: var(--ink);
  }
  .sheet {
    position: relative; width: 1200px; height: 1200px;
    display: flex; flex-direction: column; align-items: center; justify-content: center; gap: 70px;
  }
  .card {
    position: relative; width: 760px; height: 430px;
    background: var(--card); border-radius: 26px; overflow: hidden;
    box-shadow: 0 6px 18px rgba(0,0,0,0.12);
  }
  .card-band { position: absolute; inset: 0; width: 100%; height: 100%; }
  .brand {
    display: flex; flex-direction: column; align-items: center; gap: 12px;
  }
  .brand-mark {
    width: 34px; height: 34px; border-radius: 50%; background: var(--brand-blue);
  }
  .brand-name {
    font-size: 25px; color: var(--brand-blue); letter-spacing: 0.5px; white-space: nowrap;
  }
  .brand-rule { width: 330px; height: 1px; background: var(--ink); opacity: 0.6; }

  .card--back .brand {
    position: absolute; left: 50%; top: 44%; transform: translate(-50%, -50%);
  }

  .card--front .brand {
    position: absolute; left: 30px; top: 50%; transform: translateY(-58%); width: 345px;
  }
  .card--front .brand-name { font-size: 19px; letter-spacing: 0.3px; }
  .card--front .brand-rule { width: 290px; }
  .divider {
    position: absolute; left: 395px; top: 0; width: 1px; height: 74%;
    background: var(--divider);
  }
  .contact { position: absolute; left: 425px; top: 52px; width: 320px; }
  .contact-name { font-size: 27px; color: var(--brand-blue); line-height: 1.1; }
  .contact-creds, .contact-role { font-size: 11px; line-height: 1.45; }
  .contact-creds { margin-top: 6px; }
  .contact-lines { list-style: none; margin-top: 18px; }
  .contact-lines li {
    display: flex; align-items: center; gap: 12px; font-size: 15px; line-height: 1.55;
  }
  .contact-lines svg { width: 16px; height: 16px; flex: none; fill: var(--deep-blue); }
  .address { margin-top: 6px; font-size: 15px; line-height: 1.55; }
  .website {
    position: absolute; right: 36px; bottom: 28px;
    color: #ffffff; font-size: 15px; letter-spacing: 0.3px; white-space: nowrap;
  }
</style>
</head>
<body>
<main class="sheet">

  <section class="card card--back" aria-label="Card back">
    <svg class="card-band" viewBox="0 0 760 430" preserveAspectRatio="none" aria-hidden="true">
      <polygon points="0,418 560,418 600,400 760,400 760,430 0,430" fill="var(--steel-gray)"/>
      <polygon points="0,412 540,412 590,386 610,386 560,430 0,430" fill="var(--deep-blue)"/>
    </svg>
    <div class="brand">
      <span class="brand-mark"></span>
      <span class="brand-name">Harborview Nest Advisors, LLC</span>
      <span class="brand-rule"></span>
    </div>
  </section>

  <section class="card card--front" aria-label="Card front">
    <svg class="card-band" viewBox="0 0 760 430" preserveAspectRatio="none" aria-hidden="true">
      <polygon points="0,422 760,422 760,430 0,430" fill="var(--steel-gray)"/>
      <polygon points="432,330 760,330 760,430 412,430" fill="var(--deep-blue)"/>
    </svg>
    <div class="brand">
      <span class="brand-mark"></span>
      <span class="brand-name">Harborview Nest Advisors, LLC</span>
      <span class="brand-rule"></span>
    </div>
    <span class="divider"></span>
    <div class="contact">
      <h1 class="contact-name">Gregor Pelham</h1>
      <p class="contact-creds">MBA, ChFC®, CLU®</p>
      <p class="contact-role">Financial Advisor, Registered Representative</p>
      <ul class="contact-lines">
        <li>
          <svg viewBox="0 0 24 24" aria-label="Phone"><path d="M6.6 10.8a15.1 15.1 0 0 0 6.6 6.6l2.2-2.2c.3-.3.7-.4 1-.2 1.1.4 2.3.6 3.6.6.6 0 1 .4 1 1V20c0 .6-.4 1-1 1A17 17 0 0 1 3 4c0-.6.4-1 1-1h3.5c.6 0 1 .4 1 1 0 1.3.2 2.5.6 3.6.1.3 0 .7-.2 1z"/></svg>
          (555) 318-2946
        </li>
        <li>
          <svg viewBox="0 0 24 24" aria-label="Fax"><path d="M7 3h10v5H7zM4 9h16a1 1 0 0 1 1 1v7h-3v4H6v-4H3v-7a1 1 0 0 1 1-1zm4 7v3h8v-3z"/></svg>
          (800) 555-0193
        </li>
        <li>
          <svg viewBox="0 0 24 24" aria-label="Email"><path d="M3 5h18v14H3zm2 2v.4l7 4.6 7-4.6V7z"/></svg>
          gpelham@harborviewnest.example
        </li>
      </ul>
      <p class="address">2187 Meadowlark Ridge Rd. Suite<br>K418 Virginia Beach, VA 23999</p>
    </div>
    <span class="website">www.harborviewnest.example</span>
  </section>

</main>
</body>
</html>
```